Business Card Design Project

We have 2 businesses which help each other.

Brightvale Care (providing nurses to hospitals/nursing homes etc)

and

Brightvale HR (providing nurses to our brightvale care business - but also providing workers for farms, restaurants meatworks etc)

We would like 2 separate business cards - but similar design and feel

Target Market(s)

Managers of nursing homes, hospitals, farms, meatworks, restauants

Industry/Entity Type

Business

Requirements
Must have
• both logos
https://www.filequay-example.com/s/6v4i7j2fzkpw8wx/BrightvaleHR-Logo-Horizontal.ai
https://www.filequay-example.com/s/dr33nlhq82w3z6t/46051_844932_40145_sourcefile.ai

You may edit the layout of Brightvale HR logo

Name
position
mobile
Phone
name@brightvalehr.com.au
brigthvalehr.com.au

Name
position
mobile
phone
name@brightvalecare.net.au
brightvalecare.net.au

```html
<!DOCTYPE html>
<html lang="en">
<head>
<meta charset="utf-8">
<title>Brightvale Care and Brightvale HR – Business Cards</title>
<link rel="stylesheet" href="https://fonts.googleapis.com/css2?family=Quicksand:wght@500;700&display=swap">
<style>
  :root {
    --page-bg: #e9ecef;
    --card-white: #ffffff;
    --sky-blue: #3eaee3;
    --deep-purple: #3b2d8f;
    --text-dark: #2b2b3a;
    --card-shadow: 0 6px 18px rgba(30, 40, 60, 0.18);
  }
  * { box-sizing: border-box; margin: 0; padding: 0; }
  html, body {
    width: 1200px;
    height: 960px;
    overflow: hidden;
    background: var(--page-bg);
    font-family: "Quicksand", sans-serif;
  }
  .sheet {
    position: relative;
    width: 1200px;
    height: 960px;
  }
  .card {
    position: absolute;
    width: 560px;
    height: 320px;
    box-shadow: var(--card-shadow);
    overflow: hidden;
  }

  /* Front */
  .card-front {
    left: 320px;
    top: 70px;
    background: var(--sky-blue);
    display: flex;
    align-items: center;
    justify-content: center;
  }
  .brand-lockup {
    display: flex;
    align-items: center;
    gap: 16px;
  }
  .brand-dot {
    width: 38px;
    height: 38px;
    border-radius: 50%;
    background: var(--card-white);
  }
  .brand-name {
    font-size: 50px;
    font-weight: 700;
    color: var(--deep-purple);
    letter-spacing: -1px;
    white-space: nowrap;
  }

  /* Backs */
  .card-back { top: 500px; background: var(--card-white); }
  .card-back-hr { left: 30px; }
  .card-back-care { left: 610px; }

  .holder {
    position: absolute;
    left: 40px;
    top: 36px;
    color: var(--deep-purple);
  }
  .holder-name {
    font-size: 21px;
    font-weight: 700;
    line-height: 1.1;
  }
  .holder-role {
    font-size: 18px;
    font-weight: 500;
    line-height: 1.25;
  }
  .divider {
    position: absolute;
    left: 40px;
    top: 110px;
    width: 280px;
    border-top: 3px dotted var(--deep-purple);
  }
  .contact-list {
    position: absolute;
    left: 40px;
    top: 130px;
    list-style: none;
  }
  .contact-item {
    display: flex;
    align-items: center;
    gap: 12px;
    height: 34px;
    font-size: 16px;
    font-weight: 500;
    color: var(--text-dark);
    white-space: nowrap;
  }
  .contact-icon {
    width: 15px;
    height: 15px;
    flex: none;
  }
  .contact-icon * { fill: var(--deep-purple); }
  .back-mark {
    position: absolute;
    right: 32px;
    top: 86px;
    width: 150px;
    display: flex;
    flex-direction: column;
    align-items: center;
    gap: 12px;
  }
  .back-mark-dot {
    width: 112px;
    height: 112px;
    border-radius: 50%;
    background: var(--sky-blue);
  }
  .back-mark-name {
    font-size: 16px;
    font-weight: 700;
    color: var(--deep-purple);
    white-space: nowrap;
  }
</style>
</head>
<body>
<main class="sheet">
  <section class="card card-front" aria-label="Brightvale Care card front">
    <div class="brand-lockup">
      <span class="brand-dot" aria-hidden="true"></span>
      <span class="brand-name">Brightvale Care</span>
    </div>
  </section>

  <section class="card card-back card-back-hr" aria-label="Brightvale HR card back">
    <div class="holder">
      <p class="holder-name">Daniel Hart</p>
      <p class="holder-role">Director</p>
    </div>
    <div class="divider"></div>
    <ul class="contact-list">
      <li class="contact-item">
        <svg class="contact-icon" viewBox="0 0 24 24" aria-hidden="true"><path d="M6.6 10.8a15 15 0 0 0 6.6 6.6l2.2-2.2a1 1 0 0 1 1-.25 11.4 11.4 0 0 0 3.6.57 1 1 0 0 1 1 1V20a1 1 0 0 1-1 1A17 17 0 0 1 3 4a1 1 0 0 1 1-1h3.5a1 1 0 0 1 1 1c0 1.25.2 2.45.57 3.6a1 1 0 0 1-.25 1z"/></svg>
        <span>+ 61 400 555 123</span>
      </li>
      <li class="contact-item">
        <svg class="contact-icon" viewBox="0 0 24 24" aria-hidden="true"><path d="M7 1h10a2 2 0 0 1 2 2v18a2 2 0 0 1-2 2H7a2 2 0 0 1-2-2V3a2 2 0 0 1 2-2zm0 3v14h10V4zm5 15.5a1.2 1.2 0 1 0 0 2.4 1.2 1.2 0 0 0 0-2.4z"/></svg>
        <span>+ 61 (0)2 5550 1234</span>
      </li>
      <li class="contact-item">
        <svg class="contact-icon" viewBox="0 0 24 24" aria-hidden="true"><path d="M2 5h20v14H2zm2 2v.5l8 5 8-5V7zm0 2.9V17h16V9.9l-8 5z"/></svg>
        <span>name@brightvalehr.com.au</span>
      </li>
      <li class="contact-item">
        <svg class="contact-icon" viewBox="0 0 24 24" aria-hidden="true"><path d="M12 2a10 10 0 1 0 0 20 10 10 0 0 0 0-20zm0 2a8 8 0 0 1 0 16 8 8 0 0 1 0-16zM4 11h16v2H4zm7-7h2v16h-2z"/></svg>
        <span>www.brigthvalehr.com.au</span>
      </li>
    </ul>
    <div class="back-mark">
      <span class="back-mark-dot" aria-hidden="true"></span>
      <span class="back-mark-name">Brightvale HR</span>
    </div>
  </section>

  <section class="card card-back card-back-care" aria-label="Brightvale Care card back">
    <div class="holder">
      <p class="holder-name">Daniel Hart</p>
      <p class="holder-role">Director</p>
    </div>
    <div class="divider"></div>
    <ul class="contact-list">
      <li class="contact-item">
        <svg class="contact-icon" viewBox="0 0 24 24" aria-hidden="true"><path d="M6.6 10.8a15 15 0 0 0 6.6 6.6l2.2-2.2a1 1 0 0 1 1-.25 11.4 11.4 0 0 0 3.6.57 1 1 0 0 1 1 1V20a1 1 0 0 1-1 1A17 17 0 0 1 3 4a1 1 0 0 1 1-1h3.5a1 1 0 0 1 1 1c0 1.25.2 2.45.57 3.6a1 1 0 0 1-.25 1z"/></svg>
        <span>+ 61 400 555 123</span>
      </li>
      <li class="contact-item">
        <svg class="contact-icon" viewBox="0 0 24 24" aria-hidden="true"><path d="M7 1h10a2 2 0 0 1 2 2v18a2 2 0 0 1-2 2H7a2 2 0 0 1-2-2V3a2 2 0 0 1 2-2zm0 3v14h10V4zm5 15.5a1.2 1.2 0 1 0 0 2.4 1.2 1.2 0 0 0 0-2.4z"/></svg>
        <span>+ 61 (0)2 5550 1234</span>
      </li>
      <li class="contact-item">
        <svg class="contact-icon" viewBox="0 0 24 24" aria-hidden="true"><path d="M2 5h20v14H2zm2 2v.5l8 5 8-5V7zm0 2.9V17h16V9.9l-8 5z"/></svg>
        <span>name@brightvalecare.net.au</span>
      </li>
      <li class="contact-item">
        <svg class="contact-icon" viewBox="0 0 24 24" aria-hidden="true"><path d="M12 2a10 10 0 1 0 0 20 10 10 0 0 0 0-20zm0 2a8 8 0 0 1 0 16 8 8 0 0 1 0-16zM4 11h16v2H4zm7-7h2v16h-2z"/></svg>
        <span>www.brightvalecare.net.au</span>
      </li>
    </ul>
    <div class="back-mark">
      <span class="back-mark-dot" aria-hidden="true"></span>
      <span class="back-mark-name">Brightvale Care</span>
    </div>
  </section>
</main>
</body>
</html>
```